Brightway Coordination Group Business card

We wish to have a professional Business card to present to large Corporate CEO's ASAP.

Our web site helps explain our business www.brightwaycg.org

Brightway Coordination Group was established after we discovered how difficult it is to organise outsourced services while heading up a business or company.

We act as a facilitator for businesses who don't have the desire, expertise or recourses to manage their own systems and meet all their requirements.

We provide an all in one facility management solution for all types of businesses. We manage schedules, contractors and costs on behalf of businesses and their needs and wants.

Having an extensive network ensures we are able to connect businesses with the right service providers.

Target Market(s)

Company CEO

Industry/Entity Type

Business

Font styles to use
Sans Serif

Colors
33a6d7
f9fdfe
0355a3

Requirements
Must have
• professional design
Nice to have
• colours to match logo

```html
<!DOCTYPE html>
<html lang="en">
<head>
<meta charset="utf-8">
<title>Brightway Coordination Group – Business Card</title>
<link href="https://fonts.googleapis.com/css2?family=Lato:wght@400;700&display=swap" rel="stylesheet">
<style>
  :root {
    --sky: #33a6d7;
    --sky-light: #3dbdf0;
    --paper: #f9fdfe;
    --navy: #0355a3;
    --ink: #1d1d1f;
    --ink-soft: #3a3a3c;
    --backdrop: #d9dde1;
  }
  * { margin: 0; padding: 0; box-sizing: border-box; }
  html, body {
    width: 1200px; height: 997px; overflow: hidden;
    background: var(--backdrop);
    font-family: "Lato", sans-serif;
  }
  .card {
    position: absolute;
    width: 560px; height: 320px;
    border-radius: 24px;
    box-shadow: 0 10px 30px rgba(0,0,0,0.18);
    overflow: hidden;
  }
  /* Back of card */
  .card-back {
    left: 40px; top: 170px;
    background: linear-gradient(160deg, var(--sky-light), var(--sky));
  }
  .back-brand {
    position: absolute; right: 40px; bottom: 110px;
    text-align: right;
  }
  .back-tagline {
    font-size: 12px; letter-spacing: 1.5px; color: var(--ink);
    margin-bottom: 6px;
  }
  .back-name {
    display: flex; align-items: center; gap: 10px; justify-content: flex-end;
    font-size: 19px; font-weight: 700; letter-spacing: 1px;
    color: var(--ink); text-transform: uppercase;
  }
  .brand-dot {
    width: 16px; height: 16px; border-radius: 50%;
    background: var(--navy);
  }
  /* Front of card */
  .card-front {
    left: 600px; top: 500px;
    background: var(--paper);
  }
  .front-brand {
    position: absolute; left: 70px; top: 50px;
    display: flex; align-items: center; gap: 12px;
    font-size: 22px; font-weight: 700; letter-spacing: 1px;
    color: var(--ink); text-transform: uppercase;
  }
  .front-brand .brand-dot { width: 26px; height: 26px; }
  .holder {
    position: absolute; right: 40px; top: 140px;
    font-size: 22px; letter-spacing: 1px; text-transform: uppercase;
  }
  .holder-first { color: var(--sky); }
  .holder-last { color: var(--navy); font-weight: 700; }
  .holder-rule {
    position: absolute; left: 200px; right: 40px; top: 175px;
    height: 2px; background: var(--ink);
  }
  .contact-rule {
    position: absolute; left: 40px; width: 200px; top: 205px;
    height: 2px; background: var(--ink);
  }
  .contact-list {
    position: absolute; left: 40px; top: 218px;
    list-style: none;
  }
  .contact-item {
    display: flex; align-items: center; gap: 10px;
    font-size: 14px; font-weight: 700; color: var(--ink-soft);
    height: 26px;
  }
  .contact-icon { width: 16px; height: 16px; fill: var(--navy); flex: none; }
</style>
</head>
<body>

<section class="card card-back" aria-label="Card back">
  <div class="back-brand">
    <p class="back-tagline">FACILITY COORDINATION</p>
    <p class="back-name"><span class="brand-dot"></span>Brightway Coordination Group</p>
  </div>
</section>

<section class="card card-front" aria-label="Card front">
  <div class="front-brand"><span class="brand-dot"></span>Brightway Coordination Group</div>

  <p class="holder"><span class="holder-first">Martin</span> <span class="holder-last">Caldwell</span></p>
  <div class="holder-rule"></div>

  <div class="contact-rule"></div>
  <ul class="contact-list">
    <li class="contact-item">
      <svg class="contact-icon" viewBox="0 0 16 16" aria-hidden="true"><path d="M3 1h3l1.5 4-2 1.2a9 9 0 0 0 4.3 4.3L11 8.5l4 1.5v3a2 2 0 0 1-2 2A12 12 0 0 1 1 3a2 2 0 0 1 2-2z"/></svg>
      0412 587 930
    </li>
    <li class="contact-item">
      <svg class="contact-icon" viewBox="0 0 16 16" aria-hidden="true"><path d="M6.5 9.5l3-3M7 4.5l1.5-1.5a3 3 0 0 1 4.5 4.5L11.5 9M9 11.5L7.5 13a3 3 0 0 1-4.5-4.5L4.5 7" stroke="currentColor" style="stroke:var(--navy)" stroke-width="1.8" fill="none" stroke-linecap="round"/></svg>
      www.brightwaycg.org
    </li>
    <li class="contact-item">
      <svg class="contact-icon" viewBox="0 0 16 16" aria-hidden="true"><path d="M1 3h14v10H1z"/><path d="M1.5 3.5L8 9l6.5-5.5" stroke="#f9fdfe" stroke-width="1.4" fill="none"/></svg>
      martin@brightwaycg.org
    </li>
  </ul>
</section>

</body>
</html>
```